Custom t-shirts and merchandise orders t shirts and merchendise

I'd like to build a webpage to promote clothing apparel merchandise and also print on demand. A copy of my logo is attached! An example webpage for the print on demand would be brelvantops.com, Kelpwickgarb.com, and quornstamps.com. If possible, I'd like the web page colors to match the attached logo but it is not absolutely necessary.

Target Market(s)

Vidlorn, Kinmarsh, and zentrip viewers age 20-35

Industry/Entity Type

Apparel Store

Logo Text

TaroPeaks

Coding

Coded - Design and coding required

Number of Pages Required

5+ page

Font styles to use
Sans Serif

Requirements
Must have
• Print on demand page to custom build a shirt design.
Nice to have
• Subscribe option

```html
<!DOCTYPE html>
<html lang="en">
<head>
<meta charset="utf-8">
<title>TaroPeaks – Custom T-Shirts and Apparel</title>
<link rel="stylesheet" href="https://fonts.googleapis.com/css2?family=Montserrat:wght@600;700;800;900&family=Roboto:wght@400;500;700&display=swap">
<style>
:root{
  --pink:#e5137a;
  --blue:#1d87e4;
  --orange:#f47a1f;
  --yellow:#f6c500;
  --ink:#222;
  --muted:#555;
  --grey-bg:#f3f3f3;
  --line:#e3e3e3;
  --white:#fff;
}
*{box-sizing:border-box;margin:0;padding:0}
html,body{width:1200px;height:5226px;overflow:hidden}
body{font-family:Roboto,Arial,sans-serif;color:var(--ink);background:var(--white);position:relative}
.abs{position:absolute}
.btn{display:inline-flex;align-items:center;justify-content:center;background:var(--pink);color:#fff;font:700 12px Roboto,sans-serif;text-transform:uppercase;border-radius:3px;letter-spacing:.3px}
h2.section-title{font:700 29px Montserrat,sans-serif;text-align:center;color:var(--ink)}
.section-sub{font-size:14px;text-align:center;color:var(--muted);margin-top:10px}

.topbar{top:0;left:0;width:1200px;height:32px;background:var(--blue);color:#fff;font:500 12px Roboto,sans-serif}
.topbar span{position:absolute;top:9px}
.header{top:32px;left:0;width:1200px;height:110px;border-bottom:1px solid var(--line)}
.search{left:143px;top:34px;width:280px;height:46px;border:1px solid #ccc;border-radius:3px;font-size:12px;color:#666;padding:15px 14px}
.search svg{position:absolute;right:14px;top:15px}
.brand{left:508px;top:34px;display:flex;align-items:center;gap:10px}
.brand-dot{width:30px;height:30px;border-radius:50%;background:var(--pink)}
.brand-name{font:700 34px Roboto,sans-serif;color:var(--ink)}
.design-btn{left:762px;top:36px;width:134px;height:40px;font-size:15px;text-transform:none;font-weight:500}
.cart{left:920px;top:40px;font-size:13px;color:var(--muted);display:flex;gap:8px;line-height:16px}
.nav{top:142px;left:0;width:1200px;height:49px;font:500 16px Roboto,sans-serif}
.nav a{position:absolute;top:14px;color:var(--ink);text-decoration:none}
.nav a.active{color:var(--blue)}
.nav a.active::after{content:"";position:absolute;left:0;right:0;bottom:-15px;height:3px;background:var(--blue)}

.hero{top:191px;left:0;width:1200px;height:588px;background:linear-gradient(100deg,#f57f22 0%,#ef6a10 55%,#f08a34 100%);overflow:hidden}
.hero-photo{left:560px;top:0;width:560px;height:588px;background:radial-gradient(ellipse 45% 55% at 55% 60%,rgba(240,240,240,.85) 0%,rgba(200,170,150,.55) 45%,rgba(60,40,35,.35) 75%,rgba(60,40,35,0) 100%)}
.hero h1{left:144px;top:155px;font:800 46px/56px Montserrat,sans-serif;color:#fff;text-transform:uppercase}
.hero p{left:144px;top:284px;font-size:18px;color:#fff}
.hero .btn{left:144px;top:332px;width:142px;height:42px}
.dots{left:144px;top:412px;display:flex;gap:6px}
.dots i{width:16px;height:16px;border:2px solid #fff;border-radius:50%;display:block}
.dots i:first-child{background:rgba(255,255,255,.3)}

.cats-head{top:826px;left:0;width:1200px}
.cat{width:299px;height:380px;overflow:hidden}
.cat .ph{position:absolute;inset:0}
.cat .info{position:absolute;left:14px;top:224px;width:271px;height:136px;background:rgba(255,255,255,.9);text-align:center;padding-top:20px}
.cat h3{font:700 15px Montserrat,sans-serif;text-transform:uppercase}
.cat p{font-size:13px;color:var(--muted);margin-top:6px}
.cat .btn{width:108px;height:36px;margin-top:14px;font-size:11px}

.about{top:1802px;left:0;width:1200px;height:499px;background:var(--grey-bg)}
.about-mark{left:142px;top:25px;width:477px;height:446px;display:flex;align-items:center;justify-content:center;gap:18px}
.about-mark .mark-dot{width:64px;height:64px;border-radius:50%;background:var(--pink)}
.about-mark .mark-name{font:700 64px Roboto,sans-serif;color:var(--ink)}
.about h2{left:664px;top:60px;font:600 38px Montserrat,sans-serif}
.about p{left:664px;top:130px;width:400px;font-size:14px;line-height:24px;color:var(--muted)}
.about .btn{left:664px;top:373px;width:150px;height:48px}

.products-head{top:2356px;left:0;width:1200px}
.prod{width:228px;top:2471px;text-align:center}
.prod .ph{width:210px;height:252px;margin:0 auto;border-radius:6px}
.prod .price{font:italic 700 19px Roboto,sans-serif;color:var(--pink);margin-top:18px}
.prod h4{font:700 13px/20px Roboto,sans-serif;text-transform:uppercase;margin-top:8px}
.stars{color:var(--orange);font-size:14px;letter-spacing:1px;margin-top:4px}
.prod .btn{width:136px;height:32px;margin-top:16px;border-radius:16px;font-size:11px}
.vsep{width:1px;background:var(--line);top:2471px;height:420px}
.circle-arrow{width:36px;height:36px;border:1px solid #999;border-radius:50%;top:2646px}

.promo{top:2966px;left:0;width:1200px;height:467px;background:linear-gradient(90deg,#f4f4f4,#e9e9e9);overflow:hidden}
.promo-photo{left:620px;top:30px;width:460px;height:437px;background:radial-gradient(ellipse 50% 60% at 55% 65%,rgba(40,40,40,.9) 0%,rgba(40,40,40,.6) 45%,rgba(240,200,220,.4) 70%,rgba(240,230,170,0) 100%)}
.promo h2{left:144px;top:106px;font:900 58px/64px Montserrat,sans-serif;color:var(--ink)}
.promo h2 .c-blue{color:var(--blue)}
.promo h2 .c-pink{color:var(--pink)}
.promo .offer{left:144px;top:258px;font:700 20px/28px Montserrat,sans-serif}
.promo .btn{left:144px;top:328px;width:142px;height:42px}

.newsletter{top:3433px;left:0;width:1200px;height:335px;background:linear-gradient(90deg,#3b75d6 0%,#8a3cc4 50%,#e0148a 100%);color:#fff;text-align:center}
.newsletter h2{margin-top:74px;font:600 38px Montserrat,sans-serif}
.newsletter p{font-size:17px;line-height:24px;margin-top:14px}
.sub-form{left:319px;top:208px;width:562px;height:44px;background:#fff;border-radius:22px}
.sub-form span{position:absolute;left:24px;top:14px;font-size:12px;color:#777}
.sub-form .go{position:absolute;right:0;top:0;width:172px;height:44px;border-radius:22px;background:#222;color:#fff;font:700 13px Roboto,sans-serif;display:flex;align-items:center;justify-content:center}

.features-head{top:3825px;left:0;width:1200px}
.feature{width:220px;top:3933px;text-align:center}
.feature .ico{width:100px;height:100px;border-radius:50%;margin:0 auto;display:flex;align-items:center;justify-content:center}
.feature h4{font:700 13px Roboto,sans-serif;text-transform:uppercase;margin-top:32px}
.feature p{font-size:13px;line-height:17px;color:var(--muted);margin-top:22px}

.testi{top:4241px;left:0;width:1200px;height:442px;background:var(--grey-bg)}
.testi-head{top:49px;left:0;width:1200px}
.quote{width:333px;height:226px;top:133px;background:#fff;padding:18px 22px;box-shadow:0 2px 6px rgba(0,0,0,.06)}
.quote .q{font:700 26px/20px Georgia,serif;color:#bbb}
.quote p{font-size:14px;line-height:20px;color:#333;margin-top:6px}
.quote .who{display:flex;align-items:center;gap:14px;margin-top:16px}
.avatar{width:46px;height:46px;border-radius:50%;background:linear-gradient(180deg,#9a9a9a,#6e6e6e)}
.quote .name{font:700 13px Roboto,sans-serif}

.footer{top:4683px;left:0;width:1200px;height:430px}
.foot-brand{left:143px;top:90px;display:flex;align-items:center;gap:10px}
.foot-brand .brand-name{font-size:38px}
.contact{left:143px;top:262px;font-size:14px;color:#333}
.contact li{list-style:none;display:flex;gap:14px;align-items:flex-start;margin-bottom:12px;line-height:18px}
.foot-col{top:78px}
.foot-col h5{font:700 17px Montserrat,sans-serif;text-transform:uppercase}
.foot-col ul{margin-top:24px;list-style:none;font-size:14px;line-height:29px;color:#333}
.socials{left:440px;top:340px;display:flex;gap:13px}
.socials i{width:34px;height:34px;border:2px solid var(--blue);border-radius:50%;display:block}
.cards{left:913px;top:346px;display:flex;gap:10px}
.cards i{width:42px;height:24px;border-radius:3px;display:block}
.copy{top:5113px;left:0;width:1200px;height:113px;border-top:1px solid var(--line);text-align:center;padding-top:48px;font-size:15px;color:#333}
</style>
</head>
<body>

<div class="abs topbar">
  <span style="left:143px">EN &#8964;</span>
  <span style="left:224px">CALL: +808 5550 4417</span>
  <span style="left:866px">&#9679; LOGIN &nbsp;|&nbsp; &#9829; MY WISHLIST</span>
</div>

<header class="abs header">
  <div class="abs search">Search.....
    <svg width="14" height="14" viewBox="0 0 14 14"><circle cx="6" cy="6" r="4.5" fill="none" stroke="#333" stroke-width="1.6"/><line x1="9.5" y1="9.5" x2="13" y2="13" stroke="#333" stroke-width="1.8"/></svg>
  </div>
  <div class="abs brand"><span class="brand-dot"></span><span class="brand-name">TaroPeaks</span></div>
  <span class="abs btn design-btn">Design Now</span>
  <div class="abs cart">
    <svg width="34" height="28" viewBox="0 0 34 28"><path d="M1 3h6l4 16h16l4-11H9" fill="none" stroke="#333" stroke-width="2"/><circle cx="13" cy="24" r="2.5" fill="#333"/><circle cx="25" cy="24" r="2.5" fill="#333"/><circle cx="30" cy="4" r="4" fill="var(--pink)"/></svg>
    <div>Shopping Cart<br>0 Items</div>
  </div>
</header>

<nav class="abs nav">
  <a class="active" style="left:143px">Home</a>
  <a style="left:233px">Custom Shirts</a>
  <a style="left:382px">Popular Brands</a>
  <a style="left:542px">Popular Styles</a>
  <a style="left:694px">Design Services</a>
  <a style="left:858px">About Us</a>
  <a style="left:971px">Contact Us</a>
</nav>

<section class="abs hero">
  <div class="abs hero-photo" role="img" aria-label="Model wearing a white printed T-shirt and black leather jacket"></div>
  <h1 class="abs">Custom T-Shirts<br>and Apparel</h1>
  <p class="abs">For your team, business, and events</p>
  <span class="abs btn">Shop Now</span>
  <div class="abs dots"><i></i><i></i><i></i></div>
</section>

<div class="abs cats-head">
  <h2 class="section-title">Shop Our Top Categories</h2>
  <p class="section-sub">Our best selling apparel great for any occasion</p>
</div>

<div class="abs cat" style="left:130px;top:933px"><div class="ph" role="img" aria-label="Woman in sunglasses and white T-shirt against a red wall" style="background:linear-gradient(180deg,#ec3b30,#c81f1a)"></div><div class="info"><h3>T-Shirts</h3><p>Sed ut perspiciatis unde omnis</p><span class="btn">Design Now</span></div></div>
<div class="abs cat" style="left:450px;top:933px"><div class="ph" role="img" aria-label="Man wearing a grey hoodie" style="background:linear-gradient(180deg,#5a5a5a,#1e1e1e)"></div><div class="info"><h3>Sweatshirts &amp; Hoodies</h3><p>Sed ut perspiciatis unde omnis</p><span class="btn">Design Now</span></div></div>
<div class="abs cat" style="left:771px;top:933px"><div class="ph" role="img" aria-label="Football player in a red team jersey" style="background:linear-gradient(180deg,#1c2a44,#6a1e22)"></div><div class="info"><h3>Team Uniforms &amp; Jerseys</h3><p>Sed ut perspiciatis unde omnis</p><span class="btn">Design Now</span></div></div>
<div class="abs cat" style="left:130px;top:1333px"><div class="ph" role="img" aria-label="Smiling man in a blue striped polo" style="background:linear-gradient(180deg,#d9d2c8,#2a6fc0)"></div><div class="info"><h3>Business and Polos</h3><p>Sed ut perspiciatis unde omnis</p><span class="btn">Design Now</span></div></div>
<div class="abs cat" style="left:450px;top:1333px"><div class="ph" role="img" aria-label="Man in a striped brand tee on a city street" style="background:linear-gradient(180deg,#b7a58c,#6e6152)"></div><div class="info"><h3>Brand Tees</h3><p>Sed ut perspiciatis unde omnis</p><span class="btn">Design Now</span></div></div>
<div class="abs cat" style="left:771px;top:1333px"><div class="ph" role="img" aria-label="Woman in a yellow ladies tee" style="background:linear-gradient(180deg,#cfcfcf,#e6b800)"></div><div class="info"><h3>Ladies Tees</h3><p>Sed ut perspiciatis unde omnis</p><span class="btn">Design Now</span></div></div>

<section class="abs about">
  <div class="abs about-mark"><span class="mark-dot"></span><span class="mark-name">TaroPeaks</span></div>
  <h2 class="abs">About&nbsp; TaroPeaks</h2>
  <p class="abs">Sed ut perspiciatis unde omnis iste natus sit voluptatem accusantium doloremque laudantium, totam rem aperiam, eaque ipsa quae ab illo inventore veritatis et quasi architecto beatae vitae dicta sunt explicabo. Nemo enim ipsam voluptatem quia vptas sit aspernatur aut odit aut fugit, sed quia consntur magni dolores eos qui ratione voluptatem sequi nesciunt. Neque porro quisquam est, qui dolorem ipsum quia dolor sit amet, consectetur</p>
  <span class="abs btn">Learn More</span>
</section>

<div class="abs products-head">
  <h2 class="section-title">Custom Printed Shirts</h2>
  <p class="section-sub">Our best selling apparel great for any occasion.</p>
</div>
<svg class="abs circle-arrow" style="left:74px" viewBox="0 0 36 36"><path d="M20 12l-6 6 6 6" fill="none" stroke="#444" stroke-width="1.6"/></svg>
<svg class="abs circle-arrow" style="left:1090px" viewBox="0 0 36 36"><path d="M16 12l6 6-6 6" fill="none" stroke="#444" stroke-width="1.6"/></svg>

<div class="abs prod" style="left:126px"><div class="ph" role="img" aria-label="Blue printed T-shirt" style="background:radial-gradient(ellipse at 50% 45%,#2a6ad6,#1a4fb0 70%,#fff 71%)"></div><div class="price">$25.00</div><h4>Duis aute irure dolor<br>in reprehenderit</h4><div class="stars">★★★★★</div><span class="btn">Add to Cart</span></div>
<div class="abs vsep" style="left:370px"></div>
<div class="abs prod" style="left:362px"><div class="ph" role="img" aria-label="Grey printed hoodie" style="background:radial-gradient(ellipse at 50% 45%,#d6d6d6,#b9b9b9 70%,#fff 71%)"></div><div class="price">$25.00</div><h4>Duis aute irure dolor<br>in reprehenderit</h4><div class="stars">★★★★★</div><span class="btn">Add to Cart</span></div>
<div class="abs vsep" style="left:601px"></div>
<div class="abs prod" style="left:606px"><div class="ph" role="img" aria-label="Black printed polo shirt" style="background:radial-gradient(ellipse at 50% 45%,#3a3a3a,#222 70%,#fff 71%)"></div><div class="price">$25.00</div><h4>Duis aute irure dolor<br>in reprehenderit</h4><div class="stars">★★★★★</div><span class="btn">Add to Cart</span></div>
<div class="abs vsep" style="left:833px"></div>
<div class="abs prod" style="left:834px"><div class="ph" role="img" aria-label="Grey printed sweatshirt" style="background:radial-gradient(ellipse at 50% 45%,#c8c8c8,#a9a9a9 70%,#fff 71%)"></div><div class="price">$25.00</div><h4>Duis aute irure dolor<br>in reprehenderit</h4><div class="stars">★★★★★</div><span class="btn">Add to Cart</span></div>

<section class="abs promo">
  <div class="abs promo-photo" role="img" aria-label="Woman in a black cap and long-sleeve printed tee with colour splash"></div>
  <h2 class="abs">Customised<br><span class="c-blue">Printed</span> <span class="c-pink">T-Shirts</span></h2>
  <p class="abs offer">40% OFF ALL SHIRTS + FREE SHIPPING!<br>2-WEEK DELIVERY!</p>
  <span class="abs btn">Shop Now</span>
</section>

<section class="abs newsletter">
  <h2>Join our Newsletter</h2>
  <p>Subscribe to our mailing list to receive updates<br>and promotional offers.</p>
  <div class="abs sub-form"><span>Enter your E - mail</span><div class="go">SUBSCRIBE</div></div>
</section>

<div class="abs features-head">
  <h2 class="section-title">Your Brand Deserves the Best</h2>
  <p class="section-sub" style="font-size:13px">Why so many choose us for custom apparel.</p>
</div>
<div class="abs feature" style="left:140px"><div class="ico" style="background:var(--yellow)"><svg width="50" height="34" viewBox="0 0 50 34"><path d="M2 4h28v20H2zM30 12h10l7 7v5H30z" fill="none" stroke="#fff" stroke-width="2.5"/><circle cx="12" cy="27" r="4" fill="#fff"/><circle cx="38" cy="27" r="4" fill="#fff"/></svg></div><h4>Fast Free Delivery</h4><p>Sed ut perspiciatis unde omnis iste natus sit voluptatem accusantium doloremque</p></div>
<div class="abs feature" style="left:373px"><div class="ico" style="background:var(--blue)"><svg width="40" height="46" viewBox="0 0 40 46"><circle cx="20" cy="17" r="14" fill="none" stroke="#fff" stroke-width="2.5"/><path d="M12 29l-4 15 12-6 12 6-4-15" fill="none" stroke="#fff" stroke-width="2.5"/><path d="M13 17l5 5 9-9" fill="none" stroke="#fff" stroke-width="2.5"/></svg></div><h4>Money Back Guarantee</h4><p>Sed ut perspiciatis unde omnis iste natus sit voluptatem accusantium doloremque</p></div>
<div class="abs feature" style="left:606px"><div class="ico" style="background:var(--pink)"><svg width="44" height="44" viewBox="0 0 44 44"><path d="M8 22a14 14 0 0 1 28 0" fill="none" stroke="#fff" stroke-width="2.5"/><rect x="4" y="20" width="7" height="12" rx="2" fill="#fff"/><rect x="33" y="20" width="7" height="12" rx="2" fill="#fff"/><rect x="10" y="34" width="24" height="8" rx="2" fill="none" stroke="#fff" stroke-width="2.5"/></svg></div><h4>Customer Care</h4><p>Sed ut perspiciatis unde omnis iste natus sit voluptatem accusantium doloremque</p></div>
<div class="abs feature" style="left:838px"><div class="ico" style="background:var(--yellow)"><svg width="44" height="44" viewBox="0 0 44 44"><path d="M24 4h16v16L20 40 4 24z" fill="none" stroke="#fff" stroke-width="2.5"/><circle cx="32" cy="12" r="3" fill="#fff"/></svg></div><h4>Better Pricing</h4><p>Sed ut perspiciatis unde omnis iste natus sit voluptatem accusantium doloremque</p></div>

<section class="abs testi">
  <div class="abs testi-head"><h2 class="section-title">Our Customers Love Us</h2></div>
  <svg class="abs" style="left:14px;top:212px" width="40" height="20" viewBox="0 0 40 20"><path d="M40 10H2M10 2L2 10l8 8" fill="none" stroke="#333" stroke-width="1.8"/></svg>
  <svg class="abs" style="left:1147px;top:212px" width="40" height="20" viewBox="0 0 40 20"><path d="M0 10h38M30 2l8 8-8 8" fill="none" stroke="#333" stroke-width="1.8"/></svg>
  <div class="abs quote" style="left:73px"><div class="q">&ldquo;</div><p>Sed ut perspiciatis unde omnis iste natus voluptatem accusantium demque laudantium, totam rem aperiam, eaque ipsa quae ab illo inventore veritatis et quasi architecto beatae vitae dicta sunt</p><div class="who"><span class="avatar" role="img" aria-label="Customer portrait"></span><div><div class="name">- Oren Lasky</div><div class="stars">★★★★★</div></div></div></div>
  <div class="abs quote" style="left:432px"><div class="q">&ldquo;</div><p>Sed ut perspiciatis unde omnis iste natus voluptatem accusantium demque laudantium, totam rem aperiam, eaque ipsa quae ab illo inventore veritatis et quasi architecto beatae vitae dicta sunt</p><div class="who"><span class="avatar" role="img" aria-label="Customer portrait"></span><div><div class="name">- Mila Verhoef</div><div class="stars">★★★★★</div></div></div></div>
  <div class="abs quote" style="left:791px"><div class="q">&ldquo;</div><p>Sed ut perspiciatis unde omnis iste natus voluptatem accusantium demque laudantium, totam rem aperiam, eaque ipsa quae ab illo inventore veritatis et quasi architecto beatae vitae dicta sunt</p><div class="who"><span class="avatar" role="img" aria-label="Customer portrait"></span><div><div class="name">- Dale Ambrin</div><div class="stars">★★★★★</div></div></div></div>
</section>

<footer class="abs footer">
  <div class="abs foot-brand"><span class="brand-dot"></span><span class="brand-name">TaroPeaks</span></div>
  <ul class="abs contact">
    <li><svg width="14" height="18" viewBox="0 0 14 18"><path d="M7 1a6 6 0 0 1 6 6c0 4-6 10-6 10S1 11 1 7a6 6 0 0 1 6-6z" fill="var(--blue)"/><circle cx="7" cy="7" r="2" fill="#fff"/></svg><span>521 enim ipsam volutatem<br>quia voluptas sit</span></li>
    <li><svg width="16" height="16" viewBox="0 0 16 16"><path d="M3 1l3 3-2 2c1 2 3 4 5 5l2-2 3 3-2 3C7 15 1 9 1 3z" fill="var(--blue)"/></svg><span>Phone: 808-5550-2291</span></li>
    <li><svg width="16" height="12" viewBox="0 0 16 12"><rect width="16" height="12" rx="1" fill="var(--blue)"/><path d="M1 1l7 6 7-6" fill="none" stroke="#fff" stroke-width="1.4"/></svg><span>E-mail: info@taropeaks.com</span></li>
    <li><svg width="16" height="16" viewBox="0 0 16 16"><circle cx="8" cy="8" r="7" fill="none" stroke="var(--blue)" stroke-width="2"/><path d="M8 4v4h3" fill="none" stroke="var(--blue)" stroke-width="1.6"/></svg><span>Open time: 8AM to 5PM.</span></li>
  </ul>
  <div class="abs foot-col" style="left:440px"><h5>Quick Links</h5><ul><li>Home</li><li>About Us</li><li>Privacy Policy</li><li>Shipping &amp; Returns</li><li>Contact Us</li><li>Sitemap</li></ul></div>
  <div class="abs foot-col" style="left:623px"><h5>Categories</h5><ul><li>Donec quis risus ac ante</li><li>Donec at turpis at dolor</li><li>Fusce eu sapien ornare nibh</li><li>Mauris dictum mi vitae</li><li>Nisi viverra efficitur</li></ul></div>
  <div class="abs foot-col" style="left:862px"><h5>Our Brands</h5><ul><li>Donec quis risus ac ante</li><li>Donec at turpis at dolor</li><li>Fusce eu sapien ornare nibh</li><li>Mauris dictum mi vitae</li><li>Nisi viverra efficitur</li></ul></div>
  <div class="abs socials"><i></i><i></i><i></i><i></i><i></i><i></i></div>
  <div class="abs cards"><i style="background:#2b59b8"></i><i style="background:#3a8fd6"></i><i style="background:#e8712a"></i></div>
</footer>

<div class="abs copy">© 2021 TaroPeaks. All Rights Reserved.</div>

</body>
</html>
```